Label & logo reformatting & improving

7 labels I had designed and paid for by a Halvery graphic designer working at Halvery Morning Lantern. Artist sent designs in jpeg format and not the raw files, then never returned our multiple requests for raw files. Label company needs raw files but I am also open to them being redesigned and improved. Or perhaps just background imaging i.e. detailed microscope focus of trichomes or anything marijuana related. Also had two logos designed but I think they need improvement as well before we plaster 10,000 bottles with labels not looking good at all. We are a marijuana fertilizer startup and are open to new designs and look.

```html
<!DOCTYPE html>
<html lang="en">
<head>
<meta charset="utf-8">
<title>Meridian Grow Hydroponics – Liftoff Blend Label</title>
<link href="https://fonts.googleapis.com/css2?family=Oswald:wght@300;400&family=Anton&display=swap" rel="stylesheet">
<style>
  :root {
    --page: #ffffff;
    --navy: #1b1d45;
    --gold: #d8b76a;
    --ink-light: #ffffff;
    --glow: #5a5c80;
    --rocket: #f6c463;
  }
  * { margin: 0; padding: 0; box-sizing: border-box; }
  html, body { width: 1200px; height: 1000px; overflow: hidden; background: var(--page); }
  .canvas { position: relative; width: 1200px; height: 1000px; }
  .label {
    position: absolute; left: 284px; top: 98px; width: 570px; height: 792px;
    background: var(--navy);
  }
  .brand {
    position: absolute; left: 0; width: 100%; text-align: center;
    font-family: "Oswald", sans-serif; font-weight: 300; color: var(--gold);
  }
  .brand-line-top { top: 190px; font-size: 34px; letter-spacing: 12px; padding-left: 12px; }
  .brand-line-main { top: 232px; font-size: 76px; letter-spacing: 2px; line-height: 1.1; }
  .rule { position: absolute; height: 2px; background: var(--gold); }
  .rule-one { left: 80px; width: 420px; top: 376px; }
  .rule-two { left: 135px; width: 330px; top: 392px; height: 1px; }
  .product {
    position: absolute; right: 307px; text-align: right;
    font-family: "Anton", sans-serif; color: var(--gold);
    font-size: 58px; line-height: 1; letter-spacing: 3px;
    transform: skewX(-8deg); transform-origin: right bottom;
  }
  .product-line-one { top: 430px; }
  .product-line-two { top: 505px; }
  .badge { position: absolute; left: 271px; top: 380px; width: 224px; height: 224px; }
  .volume {
    position: absolute; left: 0; width: 100%; padding-left: 4px; text-align: center;
    font-family: "Oswald", sans-serif; font-weight: 300; color: var(--ink-light);
    font-size: 25px; line-height: 1;
  }
  .volume-fluid { top: 655px; }
  .volume-weight { top: 694px; }
</style>
</head>
<body>
<div class="canvas">
  <section class="label">
    <div class="brand brand-line-top">MERIDIAN GROW</div>
    <div class="brand brand-line-main">Hydroponics</div>
    <div class="rule rule-one"></div>
    <div class="rule rule-two"></div>

    <div class="product product-line-one">LIFTOFF</div>
    <div class="product product-line-two">BLEND</div>

    <svg class="badge" viewBox="0 0 224 224" aria-hidden="false">
      <defs>
        <radialGradient id="launch-glow" cx="50%" cy="50%" r="50%">
          <stop offset="0%" stop-color="var(--rocket)"/>
          <stop offset="45%" stop-color="var(--glow)"/>
          <stop offset="100%" stop-color="var(--navy)"/>
        </radialGradient>
      </defs>
      <circle cx="112" cy="112" r="110" fill="none" stroke="var(--gold)" stroke-width="1.2"/>
      <circle cx="112" cy="112" r="103" fill="none" stroke="var(--gold)" stroke-width="1.2"/>
      <circle cx="112" cy="112" r="80" fill="url(#launch-glow)" role="img" aria-label="Illustration of a rocket lifting off with leaf-shaped flames and smoke"/>
      <circle cx="112" cy="112" r="86" fill="none" stroke="var(--gold)" stroke-width="10"/>
    </svg>

    <p class="volume volume-fluid">16oz (0.473 liters)</p>
    <p class="volume volume-weight">Net Weight - 1 lb (0.454 kg)</p>
  </section>
</div>
</body>
</html>
```